Website & Logo The full package New Business new design and idea

Word Press

Simple, clean and very professional and approachable if possible

I am looking for a full business concept from logo to colour pallet and everything in between.
Brand new business concept, the successful applicant may continue on as our outsourced point person for all future work.

I will have an animated explainer video going over the four keys to business success Staff, Product & Services, Marketing, Sales and why the need a coach just like a sporting team to stay focused and clear on measurable outcomes.

Just added script (pdf attachment) i will be using for the explainer video at top of site.
Updates

Target Market(s)

Small business owners in Australia

Industry/Entity Type

Business Consultant

Number of Pages Required

1 page

Font styles to use
Sans Serif

Colors

Designer to choose colors to be used in the design.

Requirements
Must have
• Word press using Divi platform
• Ball park as per pdf uploaded
• Must work on all devices
• Social links
• Clear and straight forward movement through site
• Great capture of name and email,
• Free Download
• 10 Things you can start today in your small business to get you going again!
Nice to have
• clean one page potentially
• Free files and resources page
Should not have
• boring old menu and old framing

```html
<!DOCTYPE html>
<html lang="en">
<head>
<meta charset="utf-8">
<title>Steady Ground Coaching</title>
<link rel="stylesheet" href="https://fonts.googleapis.com/css2?family=Mulish:wght@300;400;600;700;800&display=swap">
<style>
:root{
  --navy:#0c2f5e;
  --navy-deep:#082650;
  --orange:#f39021;
  --orange-dark:#e8831a;
  --charcoal:#393939;
  --grey-band:#ececec;
  --grey-panel:#e6e6e6;
  --text:#333;
  --muted:#555;
  --white:#fff;
}
*{box-sizing:border-box;margin:0;padding:0}
html,body{width:1200px;height:4146px;overflow:hidden}
body{font-family:'Mulish',sans-serif;color:var(--text);background:var(--white);position:relative}
section,header,footer{position:absolute;left:0;width:1200px}
.wrap{position:absolute;left:143px;width:912px}

/* hero */
.hero{top:0;height:614px;background:linear-gradient(135deg,#1e5a93 0%,#14487e 45%,#0f3c6d 100%);overflow:hidden}
.hero-photo{position:absolute;inset:0;background:radial-gradient(ellipse at 62% 30%,rgba(70,130,190,.55),transparent 55%),radial-gradient(ellipse at 10% 80%,rgba(40,100,70,.35),transparent 40%)}
.topbar{position:absolute;left:143px;top:0;width:912px;height:77px;border-bottom:1px solid rgba(255,255,255,.6)}
.brand{position:absolute;left:0;top:16px;font-size:33px;font-weight:400;color:var(--white)}
.nav{position:absolute;right:0;top:30px;display:flex;gap:34px;font-size:13px;color:var(--white)}
.nav .active{color:var(--orange);text-decoration:underline}
.play{position:absolute;left:578px;top:288px;width:44px;height:44px}
.hero-title{position:absolute;top:344px;width:1200px;text-align:center;color:var(--white);font-size:25px;font-weight:600;line-height:33px}
.field{position:absolute;top:426px;height:42px;background:var(--white);border-radius:2px;font-size:14px;color:#444;padding:13px 16px}
.field.name{left:256px;width:239px}
.field.email{left:511px;width:240px}
.cta{position:absolute;top:426px;left:767px;width:175px;height:42px;background:var(--orange);color:var(--white);font-weight:700;font-size:16px;text-align:center;line-height:42px;border-radius:2px}

/* welcome */
.welcome{top:614px;height:396px}
.h-navy{color:var(--navy);font-weight:600}
.welcome h2{position:absolute;left:143px;top:72px;font-size:34px}
.welcome .lead{position:absolute;left:143px;top:124px;width:620px;font-size:15.5px;line-height:26px;color:#333}
.welcome .small{position:absolute;left:143px;top:236px;width:620px;font-size:11.5px;line-height:21px;color:#555}
.circle-photo{position:absolute;border-radius:50%}
.welcome .circle-photo{left:818px;top:79px;width:237px;height:237px;background:linear-gradient(160deg,#f4f4f6,#dfe3ea 60%,#c57b8d)}

/* snapshot */
.snapshot{top:1010px;height:373px;background:var(--orange);color:var(--white);text-align:center}
.snapshot h2{position:absolute;top:72px;width:1200px;font-size:33px;font-weight:600}
.snapshot p{position:absolute;left:143px;top:124px;width:912px;font-size:15.5px;line-height:26px}
.snapshot h3{position:absolute;top:246px;width:1200px;font-size:24px;font-weight:400}
.stats{position:absolute;left:143px;top:1304px;width:912px;display:flex;gap:13px}
.stat{width:218px;height:161px;background:var(--charcoal);color:var(--white);text-align:center;border-radius:2px;padding:14px 20px}
.stat b{display:block;font-size:60px;font-weight:700;line-height:70px}
.stat span{display:block;font-size:11.5px;line-height:19px;color:#ddd;margin-top:6px}

/* how it works */
.how{top:1465px;height:399px}
.how .circle-photo{left:143px;top:80px;width:238px;height:238px;background:linear-gradient(150deg,#e8e6e2,#c9c1b6 55%,#5f8fc3)}
.how h2{position:absolute;right:145px;top:112px;font-size:34px;text-align:right}
.how .sub{position:absolute;right:145px;top:166px;font-size:15.5px;text-align:right}
.how .keys{position:absolute;right:145px;top:190px;font-size:20px;color:var(--orange);font-weight:400;text-align:right}
.how .note{position:absolute;right:145px;top:228px;width:640px;font-size:12px;line-height:21px;text-align:right;color:var(--muted)}

/* offers */
.offers{top:1864px;height:490px;background:var(--grey-band)}
.card{position:absolute;top:80px;width:291px;height:330px;color:var(--white);padding:26px 20px}
.card h3{font-size:21px;font-weight:600;line-height:27px;height:92px}
.card p{font-size:11.5px;line-height:21px;margin-top:0}
.card .btn{position:absolute;left:20px;top:268px}
.card.free{left:143px;background:var(--navy)}
.card.offer{left:453px;background:var(--orange)}
.card.more{left:764px;background:var(--charcoal)}
.btn{display:inline-block;border:1px solid var(--white);color:var(--white);font-size:13px;padding:0 14px;height:40px;line-height:38px}

/* activities */
.activities{top:2354px;height:869px}
.activities .intro{position:absolute;left:143px;top:80px;width:912px;text-align:center;font-size:15.5px;line-height:26px;color:#333}
.list-panel{position:absolute;left:143px;top:180px;width:457px;height:608px;background:var(--grey-panel);padding:28px 20px}
.list-panel h4{font-size:16px;font-weight:400;margin-bottom:18px}
.list-panel ul{list-style:none}
.list-panel li{position:relative;padding-left:17px;font-size:13px;line-height:21px;color:#333;margin-bottom:21px;width:405px}
.list-panel li::before{content:"";position:absolute;left:0;top:6px;border-left:5px solid #555;border-top:4px solid transparent;border-bottom:4px solid transparent}
.activities .photo{position:absolute;left:600px;top:180px;width:455px;height:608px;background:linear-gradient(120deg,#eef0f2 0%,#dde2e6 55%,#c9cfd4 100%)}

/* application */
.application{top:3223px;height:340px;background:var(--navy);color:var(--white);text-align:center}
.application h2{position:absolute;top:76px;width:1200px;font-size:34px;font-weight:600}
.application p{position:absolute;left:143px;top:128px;width:912px;font-size:15.5px;line-height:26px}
.application .btn{position:absolute;left:552px;top:220px;width:96px;padding:0}

/* about */
.about{top:3563px;height:483px}
.about h2{position:absolute;left:143px;top:108px;font-size:34px}
.about p{position:absolute;left:143px;top:166px;width:620px;font-size:15.5px;line-height:26px;color:#333}
.about .ring{position:absolute;left:818px;top:166px;width:237px;height:237px;border-radius:50%;background:var(--orange)}
.about .portrait{position:absolute;left:860px;top:80px;width:153px;height:323px;border-radius:76px 76px 0 0;background:linear-gradient(180deg,#e7e7e7 0%,#2d3140 45%,#1d2030 100%)}

/* footer */
.site-footer{top:4046px;height:100px;background:var(--navy-deep);color:var(--white)}
.foot-nav{position:absolute;left:143px;top:35px;font-size:11.5px}
.foot-nav span{margin:0 8px}
.copy{position:absolute;left:143px;top:65px;font-size:11.5px}
.social{position:absolute;left:960px;top:40px;display:flex;gap:22px}
.social i{display:block;width:16px;height:16px;border-radius:50%;background:var(--white)}
</style>
</head>
<body>

<header class="hero">
  <div class="hero-photo" role="img" aria-label="Photo of a cheering businessman at his desk, tinted deep blue"></div>
  <div class="topbar">
    <div class="brand">Steady Ground Coaching</div>
    <nav class="nav"><span class="active">Home</span><span>About Us</span><span>Services</span><span>Contact Us</span></nav>
  </div>
  <svg class="play" viewBox="0 0 44 44" aria-label="Play video">
    <circle cx="22" cy="22" r="21" fill="#fff"/>
    <path d="M17 13 L31 22 L17 31 Z" fill="#163f70"/>
  </svg>
  <h1 class="hero-title">10 Things you can start today in your small business<br>to get you going again!</h1>
  <div class="field name">Name</div>
  <div class="field email">Email</div>
  <div class="cta">FREE DOWNLOAD</div>
</header>

<section class="welcome">
  <h2 class="h-navy">Welcome</h2>
  <p class="lead">Steady Ground Coaching is here to help, support and turn your small business around, It may not be easy, it may not be pretty, it may not be conventional or what you want to hear but my only goal is to help you succeed in your small business struggling in Australia.</p>
  <p class="small">I offer a 12 week fully supported and personally applied program, each week you complete the activities and we meet over video call where your actions are accountable and measurable. Every business and small business owner are different, so not one solution fits all, and that's exactly why I can make it personal for those who want to change and need it to happen now..</p>
  <div class="circle-photo" role="img" aria-label="Photo of a woman pinning charts to a planning wall"></div>
</section>

<section class="snapshot">
  <h2>Australian Small Business Snapshot</h2>
  <p>It's an extremely sad sign of the times when you're confronted with a myriad of 'for lease' signs in shop windows along major shopping hubs. While most businesses in Australia are small -- accounting for 97 percent of all businesses -- they're shutting their doors in alarmingly high numbers.</p>
  <h3>What is the Small Business Failure Rate?</h3>
</section>
<div class="stats">
  <div class="stat"><b>20%</b><span>of small businesses fail in their first year</span></div>
  <div class="stat"><b>30%</b><span>of small business fail in their second year</span></div>
  <div class="stat"><b>50%</b><span>of small businesses fail after five years in business</span></div>
  <div class="stat"><b>70%</b><span>Finally, 70% of small business owners fail in their 10th year in business.</span></div>
</div>

<section class="how">
  <div class="circle-photo" role="img" aria-label="Photo of a smiling businessman shaking hands"></div>
  <h2 class="h-navy">How it all works</h2>
  <div class="sub">With your permission I breakdown your</div>
  <div class="keys">BUSINESS, STAFF, PRODUCTS / SERVICES, MARKETING AND SALES</div>
  <p class="note">Under each of these four key components are up to 30 or more components including your staff training and experience, business financials, public exposure and engagement with target market, current marketing and processes required to make income.</p>
</section>

<section class="offers">
  <article class="card free">
    <h3>Giving Back Free</h3>
    <p>Steady Ground Coaching is offering 4 FREE 12-week coaching one on one support program every 3 months to struggling businesses in 2019 as our way of giving back and helping others in need, just fill out the information sheet and we will let you know as soon as possible.</p>
    <span class="btn">Learn More</span>
  </article>
  <article class="card offer">
    <h3>Special Offer - Below Cost Price $200 a week for 12 weeks</h3>
    <p>Steady Ground Coaching is offering this incredible one on one support program to only 12 small business owners in the first quarter in 2019 at below cost, so if you need help now, just fill out the information sheet and we will let you know as soon as possible.</p>
    <span class="btn">Learn More</span>
  </article>
  <article class="card more">
    <h3>Just A Bit More $400 a week for 12 weeks</h3>
    <p>Very limited on application only just 4 clients per quarter, here we provide additional one on one support each week and dive deeper into every element of your business and fast track the changes, just fill out the information sheet and we will let you know as soon as possible.</p>
    <span class="btn">Learn More</span>
  </article>
</section>

<section class="activities">
  <p class="intro">Regardless if you're a Steady Ground Free, Special Offer or Just a Bit More, Small Business Owner you all get one on one direct access to me each week along with mountains of accountable activities to turn your small business around into the dream you had hoped it could be.</p>
  <div class="list-panel">
    <h4>Activates include :</h4>
    <ul>
      <li>Getting a measurable base line of the financials and existing marketing.</li>
      <li>Discussing the past ups and downs and looking forward to the future</li>
      <li>Understanding your product or service and how it fits into the current marketplace.</li>
      <li>Looking into the staff for potential opportunities or training.</li>
      <li>Understanding market trends and embracing a SWOT analysis</li>
      <li>Looking to establish a mastermind local group with a successful business</li>
      <li>Partnership opportunities</li>
      <li>Creating and applying marketing objectives</li>
      <li>How to give more to grow</li>
      <li>External learning materials applied as per needs such as specific podcast episodes or suggested books that relate to a special need to be supported.</li>
    </ul>
  </div>
  <div class="photo" role="img" aria-label="Photo of a smiling woman in a striped top in a bright office"></div>
</section>

<section class="application">
  <h2>Application</h2>
  <p>Placements are strictly limited to 28 per quarter as they are all managed personally for the best possible outcomes. You must have internet access, put the time aside between 1-2 hours a week on video call and be open to change and motivated and accountable to succeed with every scheduled meeting.</p>
  <span class="btn">Learn More</span>
</section>

<section class="about">
  <h2 class="h-navy">About Me</h2>
  <p>I am not superman, I just found myself absorbing information over the past 10 years through some mentors and personal development and see so many small business owners struggling and I got sick of telling myself how I would change things that I eventually approached some businesses for free and asked if they needed a hand and they were over the moon, very receptive and after a 1 hour talk the immediate action taken saw some massive returns exceeding even my estimates and now I just want to help more Small Business Owners through Steady Ground Coaching support.</p>
  <div class="ring"></div>
  <div class="portrait" role="img" aria-label="Portrait of the coach in a dark suit"></div>
</section>

<footer class="site-footer">
  <div class="foot-nav">Home<span>|</span>About Us<span>|</span>Services<span>|</span>Contact Us</div>
  <div class="copy">Copyright &copy; 2018 &nbsp; Steady Ground Coaching. &nbsp; All rights reserved.</div>
  <div class="social" aria-label="Social links"><i></i><i></i><i></i></div>
</footer>

</body>
</html>
```